Thornbury Building Company - Card Design

I am looking to use the logo designs that you already did for me to develop a business card. I would like the card to have a black background and be double sided. I want white and green logo and text. I have attached an inspiration photo of a look that I like. I would like to use the Vertical Logo attached to take up the full front side of the card. On the back where I have my name and information, I would like to have the horizontal logo or maybe even just the image of the 'A' and trees without the text. I am open, but I am looking for something clean and simple and I want the green to really pop! Additional files can be found under Design #: 58302946

Target Market(s)

Homeowners

Industry/Entity Type

Construction

Contact Information for Business Card

Name: Marcus Thornbury, Title: Project Manager, Phone: 555.274.8136, Email: thornburybuildingcompany@mailvesta.com, address: 487 Larkspur Ln, Cedarvale, CA 95033, Lic# 2468317

Colors
00AB8E
00BBA5
67D7C9
C6EFE9
E9F9F6

Requirements
Nice to have
• I would like to see the logos that I have already got from ArtLoomHub, though I am open to new ones

```html
<!DOCTYPE html>
<html lang="en">
<head>
<meta charset="utf-8">
<title>Thornbury Building Company – Business Card</title>
<link href="https://fonts.googleapis.com/css2?family=Figtree:wght@400;600;700&display=swap" rel="stylesheet">
<style>
  :root {
    --canvas: #1f1f1f;
    --card-light: #3a3637;
    --card-dark: #242122;
    --green: #3fb54a;
    --white: #f4f4f4;
    --muted: #d9d9d9;
  }
  * { box-sizing: border-box; margin: 0; padding: 0; }
  html, body {
    width: 1200px; height: 1200px; overflow: hidden;
    background: var(--canvas);
    font-family: "Figtree", Arial, sans-serif;
  }
  .stage {
    width: 1200px; height: 1200px;
    display: flex; flex-direction: column; align-items: center; justify-content: center;
    gap: 60px;
  }
  .card {
    position: relative;
    width: 840px; height: 480px;
    border-radius: 4px;
    background: radial-gradient(ellipse at 45% 35%, var(--card-light) 0%, var(--card-dark) 75%);
    color: var(--white);
  }
  /* brand lockup: plain ring beside the company name */
  .brand { display: flex; align-items: center; gap: 22px; }
  .brand-ring {
    flex: none; border-radius: 50%;
    border: 6px solid var(--white);
  }
  .brand-name {
    font-weight: 700; color: var(--white);
    text-transform: uppercase; letter-spacing: 0.04em; line-height: 1.1;
  }
  .card-front { display: flex; align-items: center; justify-content: center; }
  .card-front .brand-ring { width: 96px; height: 96px; }
  .card-front .brand-name { font-size: 40px; }

  .card-back .brand {
    position: absolute; left: 520px; top: 110px; gap: 14px;
  }
  .card-back .brand-ring { width: 52px; height: 52px; border-width: 4px; }
  .card-back .brand-name { font-size: 22px; }

  .contact { position: absolute; left: 56px; top: 120px; }
  .contact-name {
    font-size: 36px; font-weight: 700; color: var(--green); line-height: 1.1;
  }
  .contact-title { font-size: 20px; color: var(--muted); margin: 6px 0 14px 4px; }
  .contact-line {
    display: flex; align-items: center; gap: 10px;
    font-size: 19px; color: var(--white); margin-bottom: 6px;
  }
  .contact-line svg { width: 18px; height: 18px; flex: none; }
  .licence { font-size: 19px; color: var(--muted); }
  .address {
    position: absolute; right: 90px; bottom: 56px;
    text-align: right; font-size: 24px; line-height: 1.3; color: var(--white);
  }
</style>
</head>
<body>
<main class="stage">
  <section class="card card-front" aria-label="Card front">
    <div class="brand">
      <span class="brand-ring"></span>
      <span class="brand-name">Thornbury<br>Building Company</span>
    </div>
  </section>

  <section class="card card-back" aria-label="Card back">
    <div class="contact">
      <h1 class="contact-name">Marcus Thornbury</h1>
      <p class="contact-title">Project Manager</p>
      <p class="contact-line">
        <svg viewBox="0 0 24 24" aria-hidden="true"><path fill="var(--green)" d="M6.6 10.8a15.1 15.1 0 0 0 6.6 6.6l2.2-2.2c.3-.3.7-.4 1-.2 1.1.4 2.3.6 3.6.6.6 0 1 .4 1 1V20c0 .6-.4 1-1 1A17 17 0 0 1 3 4c0-.6.4-1 1-1h3.5c.6 0 1 .4 1 1 0 1.3.2 2.5.6 3.6.1.3 0 .7-.2 1z"/></svg>
        555.274.8136
      </p>
      <p class="contact-line">
        <svg viewBox="0 0 24 24" aria-hidden="true"><rect x="2" y="5" width="20" height="14" rx="1.5" fill="var(--green)"/><path d="M3 6.5l9 6.5 9-6.5" fill="none" stroke="var(--card-dark)" stroke-width="1.6"/></svg>
        thornburybuildingcompany@mailvesta.com
      </p>
      <p class="licence">Lic# 2468317</p>
    </div>

    <div class="brand">
      <span class="brand-ring"></span>
      <span class="brand-name">Thornbury<br>Building Company</span>
    </div>

    <p class="address">487 Larkspur Ln, Cedarvale,<br>CA 95033</p>
  </section>
</main>
</body>
</html>
```